Cafe - A FRAME Design

Need to create an A frame for my café.
Logo available
Word document - has basic information we think would be good.

Name: Wuzzop Café

Notes from the A-frame printers.
File Requirements
• PDF without trim, crop or registration marks
• All files to be CMYK, not RGB
• All fonts converted to outlines (paths/curves)
• Embed all images and elements
• Files to be 100% scale unless otherwise specified
• 10mm Bleed
Resolution
• Bitmap images no less than 130 DPI at full size
Pantone Colours
• If required Pantone colours must be supplied

Target Market(s)

Mainly Students - University cafe

Requirements
Must have
• Cafe name: Wuzzop
Nice to have
• Might be nice to have background - that orange color same as logo - just an idea

Word document - has basic idea regarding text that should be included

```html
<!DOCTYPE html>
<html lang="en">
<head>
<meta charset="utf-8">
<title>Wuzzop Café – A-Frame Sign</title>
<link href="https://fonts.googleapis.com/css2?family=Poppins:wght@400;600;700&display=swap" rel="stylesheet">
<style>
  :root {
    --orange: #f15a22;
    --slate: #474b55;
    --paper: #ffffff;
    --sketch-light: #f3f0ee;
    --sketch-mid: #d9cfc9;
  }
  html, body {
    margin: 0;
    padding: 0;
    width: 695px;
    height: 1200px;
    overflow: hidden;
    background: var(--paper);
  }
  .sign {
    position: relative;
    width: 695px;
    height: 1200px;
    background: var(--paper);
    font-family: "Poppins", sans-serif;
    color: var(--slate);
    overflow: hidden;
  }
  .brand {
    position: absolute;
    top: 78px;
    left: 0;
    width: 100%;
    display: flex;
    justify-content: center;
    align-items: center;
    gap: 18px;
  }
  .brand-dot {
    width: 58px;
    height: 58px;
    border-radius: 50%;
    background: var(--orange);
  }
  .brand-name {
    font-weight: 700;
    font-size: 62px;
    line-height: 1;
    color: var(--slate);
    letter-spacing: -1px;
  }
  .tagline {
    position: absolute;
    top: 244px;
    left: 0;
    width: 100%;
    margin: 0;
    text-align: center;
    font-weight: 400;
    font-size: 36px;
    line-height: 1.25;
    color: var(--slate);
  }
  .tagline strong {
    font-weight: 700;
    color: var(--orange);
  }
  .sketch-area {
    position: absolute;
    left: 0;
    top: 640px;
    width: 100%;
    height: 490px;
    background:
      radial-gradient(ellipse at 8% 80%, var(--sketch-mid) 0%, transparent 45%),
      radial-gradient(ellipse at 92% 82%, var(--sketch-mid) 0%, transparent 42%),
      linear-gradient(180deg, var(--paper) 0%, var(--sketch-light) 100%);
  }
  .offerings {
    position: absolute;
    top: 386px;
    left: 0;
    width: 100%;
    display: flex;
    justify-content: center;
    gap: 58px;
  }
  .offer {
    width: 136px;
    height: 276px;
    border-radius: 68px;
    background: var(--slate);
    display: flex;
    flex-direction: column;
    align-items: center;
    box-sizing: border-box;
    padding-top: 10px;
  }
  .offer-icon {
    width: 106px;
    height: 106px;
    border-radius: 50%;
    background: var(--orange);
    border: 3px solid var(--paper);
    box-sizing: border-box;
    display: flex;
    align-items: center;
    justify-content: center;
  }
  .offer-label {
    margin-top: 42px;
    text-align: center;
    color: var(--paper);
    font-weight: 600;
    font-size: 21px;
    line-height: 1.35;
  }
  .ribbon {
    position: absolute;
    left: 50%;
    transform: translateX(-50%);
    text-align: center;
    font-weight: 600;
    color: var(--paper);
    white-space: nowrap;
  }
  .ribbon-dietary {
    top: 786px;
    width: 420px;
    height: 44px;
    line-height: 44px;
    font-size: 24px;
    background: var(--slate);
    clip-path: polygon(4% 0, 100% 0, 96% 100%, 0 100%);
  }
  .ribbon-catering {
    top: 830px;
    width: 280px;
    height: 44px;
    line-height: 44px;
    font-size: 23px;
    background: var(--orange);
    clip-path: polygon(0 0, 100% 0, 93% 100%, 7% 100%);
  }
  .location-bar {
    position: absolute;
    left: 0;
    bottom: 0;
    width: 100%;
    height: 70px;
    background: var(--orange);
    color: var(--paper);
    font-weight: 600;
    font-size: 25px;
    line-height: 70px;
    text-align: center;
  }
</style>
</head>
<body>
<main class="sign">
  <header class="brand">
    <span class="brand-dot"></span>
    <span class="brand-name">Wuzzop Catering</span>
  </header>

  <h1 class="tagline">Your <strong>environmentally</strong><br>&amp; <strong>sustainability</strong> focused cafe</h1>

  <div class="sketch-area" role="img" aria-label="Engraved sepia illustration of a coffee grinder, coffee plant leaves, scattered beans, a sack of beans and a cup of coffee"></div>

  <section class="offerings">
    <div class="offer">
      <div class="offer-icon">
        <svg width="60" height="60" viewBox="0 0 60 60" fill="none" stroke="#fff" stroke-width="2.5" stroke-linecap="round" stroke-linejoin="round">
          <path d="M24 8c-2 3 2 5 0 8M30 8c-2 3 2 5 0 8M36 8c-2 3 2 5 0 8"/>
          <path d="M12 22h32v10a14 14 0 0 1-14 14h-4a14 14 0 0 1-14-14z"/>
          <path d="M44 26h4a5 5 0 0 1 0 10h-5"/>
          <path d="M8 50h42"/>
        </svg>
      </div>
      <div class="offer-label">Specialty<br>Coffee</div>
    </div>
    <div class="offer">
      <div class="offer-icon">
        <svg width="60" height="60" viewBox="0 0 60 60" fill="none" stroke="#fff" stroke-width="2.5" stroke-linecap="round" stroke-linejoin="round">
          <rect x="10" y="10" width="8" height="16" rx="2"/>
          <path d="M8 30h44l-4 20H12z"/>
          <circle cx="26" cy="24" r="5"/>
          <circle cx="38" cy="22" r="6"/>
          <path d="M18 40h24"/>
        </svg>
      </div>
      <div class="offer-label">Fresh<br>Food</div>
    </div>
    <div class="offer">
      <div class="offer-icon">
        <svg width="60" height="60" viewBox="0 0 60 60" fill="none" stroke="#fff" stroke-width="2.5" stroke-linecap="round" stroke-linejoin="round">
          <circle cx="30" cy="12" r="3"/>
          <path d="M12 30a18 14 0 0 1 36 0z"/>
          <path d="M14 30l4 20h24l4-20"/>
          <path d="M24 32v16M30 32v16M36 32v16"/>
        </svg>
      </div>
      <div class="offer-label">Pastries<br>&amp; Drinks</div>
    </div>
  </section>

  <div class="ribbon ribbon-dietary">(Vegan &amp; GF) options available</div>
  <div class="ribbon ribbon-catering">Catering Available</div>

  <footer class="location-bar">Located @ Building 47</footer>
</main>
</body>
</html>
```